NCBG website design

We need a page template website design for a cms website. Please see the brief attached for the details.
The client is the National Copperfleece Breeders Guild which is an organisation promoting the Copperfleece Sheep Breed within Australia.
Updates

Project Deadline Extended
Reason: So that my top few designs can make changes and re-submit.

Target Market(s)

See attached brief

```html
<!DOCTYPE html>
<html lang="en">
<head>
<meta charset="utf-8">
<title>National Copperfleece Breeders Guild</title>
<link href="https://fonts.googleapis.com/css2?family=Arvo:wght@700&family=Open+Sans:wght@400;600;700&family=Arimo&display=swap" rel="stylesheet">
<style>
:root{
  --green:#17934a;
  --green-dark:#0e7f3c;
  --green-light:#1fa656;
  --yellow:#f7c72d;
  --ink:#666;
  --body-ink:#777;
  --header-bg:#f6f6f6;
  --footer-bg:#333;
  --hero-tone-a:#7c9a5e;
  --hero-tone-b:#6a8f4a;
  --sponsor-tone:#d9c6c6;
  --social:#2a6dc1;
  --white:#fff;
}
*{margin:0;padding:0;box-sizing:border-box}
html,body{width:985px;height:1200px;overflow:hidden;background:var(--white)}
body{font-family:"Open Sans",sans-serif;color:var(--ink);position:relative}

.site-header{position:absolute;left:0;top:0;width:985px;height:152px;background:linear-gradient(#fbfbfb,var(--header-bg))}
.brand{position:absolute;left:74px;top:30px;display:flex;align-items:center;gap:10px}
.brand-mark{width:40px;height:40px;background:var(--green);border-radius:50%}
.brand-name{font-weight:700;font-size:25px;color:var(--green)}
.site-title{position:absolute;left:316px;top:68px;font-family:"Arvo",serif;font-weight:700;font-size:24px;color:var(--green);letter-spacing:.3px}

.main-nav{position:absolute;left:0;top:152px;width:985px;height:48px;background:linear-gradient(var(--green-light),var(--green-dark))}
.main-nav ul{list-style:none;display:flex;position:absolute;left:71px;top:0;height:48px}
.main-nav li{height:48px;line-height:48px;padding:0 17px;font-weight:700;font-size:13.5px;color:var(--white);text-shadow:0 1px 1px rgba(0,0,0,.35);border-right:1px solid rgba(0,0,0,.12);letter-spacing:-.2px}
.main-nav li.is-active{background:var(--yellow);padding:0 19px}
.main-nav li:last-child{border-right:none}

.hero{position:absolute;left:71px;top:218px;width:843px;height:286px;background:var(--white);box-shadow:0 1px 5px rgba(0,0,0,.25)}
.hero-image{position:absolute;left:8px;top:8px;width:827px;height:270px;background:linear-gradient(160deg,var(--hero-tone-a),var(--hero-tone-b))}
.caption-band{position:absolute;left:8px;top:145px;height:49px;padding:0 20px 0 16px;background:rgba(30,30,30,.55);color:var(--white);font-weight:600;font-size:24px;line-height:49px;letter-spacing:-.3px}
.hero-dots{position:absolute;left:387px;top:262px;display:flex;gap:5px}
.hero-dots span{width:13px;height:13px;border-radius:50%;background:rgba(255,255,255,.6)}
.hero-dots span:first-child{background:var(--white)}

.feature{position:absolute;top:548px;width:220px;text-align:center}
.feature-icon{width:76px;height:76px;margin:0 auto;border:1px solid var(--green);border-radius:50%;padding:4px}
.feature-icon div{width:66px;height:66px;border-radius:50%;background:var(--green);display:flex;align-items:center;justify-content:center}
.feature h3{font-weight:400;font-size:18px;color:var(--green);margin-top:6px}
.feature p{font-size:12px;line-height:21px;color:var(--ink);margin-top:6px}

.welcome{position:absolute;left:71px;top:776px;width:500px}
.section-title{font-weight:400;font-size:22px;color:var(--green)}
.welcome p{font-size:11.5px;line-height:20.7px;margin-top:9px;word-break:break-all;color:var(--body-ink)}
.welcome p:first-of-type{margin-top:16px}

.sponsors{position:absolute;left:629px;top:776px;width:284px}
.slider-arrows{position:absolute;right:0;top:6px;display:flex;gap:6px}
.slider-arrows span{width:20px;height:20px;background:#8a8a8a;display:flex;align-items:center;justify-content:center}
.sponsor-ad{position:absolute;left:7px;top:51px;width:276px;height:208px;background:var(--sponsor-tone)}

.site-footer{position:absolute;left:0;top:1100px;width:985px;height:100px;background:var(--footer-bg);font-family:"Arimo",sans-serif;color:var(--white);font-size:12px}
.footer-nav{position:absolute;left:71px;top:29px}
.copyright{position:absolute;left:71px;top:59px}
.social-badge{position:absolute;left:780px;top:29px;width:52px;height:52px;border-radius:50%;background:var(--social)}
</style>
</head>
<body>
<header class="site-header">
  <div class="brand"><span class="brand-mark"></span><span class="brand-name">Copperfleece</span></div>
  <div class="site-title">NATIONAL COPPERFLEECE BREEDERS GUILD</div>
</header>
<nav class="main-nav">
  <ul>
    <li class="is-active">HOME</li><li>ABOUT</li><li>SEARCH</li><li>MEMBER SERVICES</li><li>STUD PAGES</li><li>NEWS</li><li>SALES</li><li>LINKS</li><li>CONTACT</li>
  </ul>
</nav>
<section class="hero">
  <div class="hero-image" role="img" aria-label="Photo: flock of sheep grazing in a green paddock"></div>
  <div class="caption-band">PROIN GRAVIDA NIBH VEL VELIT</div>
  <div class="hero-dots"><span></span><span></span><span></span><span></span></div>
</section>

<div class="feature" style="left:51px">
  <div class="feature-icon"><div><svg width="32" height="32" viewBox="0 0 32 32" fill="none" stroke="#fff" stroke-width="2.5" stroke-linecap="round"><path d="M8 5l4 0 2 6-3 2c1 3 4 6 7 7l2-3 6 2v4c0 2-2 3-4 3C13 26 5 18 5 8c0-2 1-3 3-3z" fill="#fff" stroke="none"/><path d="M19 9a5 5 0 0 1 4 4M19 4a10 10 0 0 1 9 9"/></svg></div></div>
  <h3>Prime Lamb Helpline</h3>
  <p>Typi non habent claritatem<br>insitam; est legentis</p>
</div>
<div class="feature" style="left:275px">
  <div class="feature-icon"><div><svg width="34" height="34" viewBox="0 0 34 34" fill="none" stroke="#fff" stroke-width="2"><rect x="4" y="6" width="26" height="24" rx="2"/><line x1="4" y1="12" x2="30" y2="12"/><line x1="10" y1="3" x2="10" y2="8"/><line x1="24" y1="3" x2="24" y2="8"/><g fill="#fff" stroke="none"><rect x="8" y="15" width="3" height="3"/><rect x="13" y="15" width="3" height="3"/><rect x="18" y="15" width="3" height="3"/><rect x="23" y="15" width="3" height="3"/><rect x="8" y="20" width="3" height="3"/><rect x="13" y="20" width="3" height="3"/><rect x="18" y="20" width="3" height="3"/><rect x="23" y="20" width="3" height="3"/><rect x="8" y="25" width="3" height="3"/><rect x="13" y="25" width="3" height="3"/></g></svg></div></div>
  <h3>Events</h3>
  <p>Typi non habent claritatem<br>insitam; est legentis</p>
</div>
<div class="feature" style="left:506px">
  <div class="feature-icon"><div><svg width="34" height="34" viewBox="0 0 34 34" fill="#fff"><circle cx="17" cy="11" r="7"/><path d="M4 33c0-8 6-12 13-12s13 4 13 12z"/></svg></div></div>
  <h3>Members</h3>
  <p>Typi non habent claritatem<br>insitam; est legentis</p>
</div>
<div class="feature" style="left:721px">
  <div class="feature-icon"><div><svg width="34" height="30" viewBox="0 0 34 30" fill="none" stroke="#fff" stroke-width="2"><rect x="6" y="4" width="25" height="22" rx="1"/><path d="M6 10H3v14a2 2 0 0 0 4 0"/><rect x="10" y="8" width="8" height="7" fill="#fff"/><line x1="21" y1="9" x2="27" y2="9"/><line x1="21" y1="13" x2="27" y2="13"/><line x1="10" y1="18" x2="27" y2="18"/><line x1="10" y1="22" x2="27" y2="22"/></svg></div></div>
  <h3>News</h3>
  <p>Typi non habent claritatem<br>insitam; est legentis</p>
</div>

<section class="welcome">
  <h2 class="section-title">Welcome to our website</h2>
  <p>Mirum est notare quam littera gothica, quam nunc putamus parum claram, anteposuerit litteriarum formas humanitatis per seacula quarta decima et quinta decima. Nam liber tempor cum soluta nobis eleifend option congue nihil imperdiet doming id quod mazim placerat facer possim assum. Typi non habent claritatem insitam; est usus legentis in iis qiui facit eorum claritatem. Investigationes demonstraverunt lectores legere me lius.</p>
  <p>Nam liber tempor cum soluta nobis eleifend option conngue nhil imperdiet doming id quiod mazim placerat facer possim assum. Typi non habent claritatem insitam; est usus legentis in iis qui facit eorum claritatem. Investigationes demonstraverunt lectores legere me lius quod ii legunt saepius. Claritas est etiam processus dynamicus, qui sequitur mutationem consuetudium lectorum. Mirum est notare quam littera gothica</p>
</section>

<aside class="sponsors">
  <h2 class="section-title">Sponsers</h2>
  <div class="slider-arrows">
    <span><svg width="8" height="10" viewBox="0 0 8 10" fill="none" stroke="#fff" stroke-width="1.5"><path d="M6 1L2 5l4 4"/></svg></span>
    <span><svg width="8" height="10" viewBox="0 0 8 10" fill="none" stroke="#fff" stroke-width="1.5"><path d="M2 1l4 4-4 4"/></svg></span>
  </div>
  <div class="sponsor-ad" role="img" aria-label="Sponsor advertisement for Karri Ridge Cattle Co: semen for sale, photo of the bull Brookvale Ranger H006"></div>
</aside>

<footer class="site-footer">
  <div class="footer-nav">Home | About | Search | Member Services | Stud Pages | News | Sales | Links | Contact</div>
  <div class="copyright">Copyright © 2013. All Rights Reserved.</div>
  <div class="social-badge"></div>
</footer>
</body>
</html>
```